Velour Detailing – Premium Automotive Detailing Studio Website Design

We're launching a premium automotive detailing studio called Velour Detailing, and we’re looking for a clean, minimal, and high-end website design (desktop + mobile version). The studio targets owners of luxury vehicles who care deeply about aesthetics, perfection, and exceptional service.
This project is about more than just showing services , it should feel like a luxury experience from the very first second. The design should be modern, minimalistic, elegant, and clearly aimed at an upscale market.
We’re looking for a designer who can translate our physical studio’s premium interior and architectural feel into a digital presence.
What we want the website to feel like:
Clean and modern
Professional and luxurious
Minimal and not cluttered
Light animations or transitions to add polish
Stylish and cinematic
Design freedom:
We trust your design direction. We are not providing strict color codes or layout instructions, we want you to create what you believe works best based on our brand positioning and target audience. Just keep it premium, modern, and well-organized.
What the website should include:
Hero section with a bold visual (image or video)
About the Studio — a few blocks explaining our story and focus on quality
Service Overview — clearly showing what we offer (detailing, ceramic coating, interior, etc.)
Gallery/Showcase — show off our work with cars, interior, and the space itself
Client Lounge Area — mention comfort, coffee, and waiting space
Testimonials — social proof from satisfied clients
Location & contact section — map, address, contact form
Footer, simple with nav, contact info, and optional social media
Target audience:
Owners of high-end vehicles (Valtrane, Korvel, etc.)
Car collectors and detailing enthusiasts
People looking for premium-level service and presentation
Brands/creators booking our photo studio

```html
<!DOCTYPE html>
<html lang="en">
<head>
<meta charset="utf-8">
<title>Velour Detailing – Premium Automotive Detailing Studio</title>
<link rel="stylesheet" href="https://fonts.googleapis.com/css2?family=Chakra+Petch:wght@500;600;700&family=Inter:wght@400;500;600;700&display=swap">
<style>
:root{
  --bg:#151515;
  --bg-deep:#0d0d0d;
  --bg-band:#1b1b1b;
  --card:#222222;
  --line:#3a3a3a;
  --text:#ffffff;
  --muted:#a9a9a9;
  --accent:#d3262e;
  --star:#f2b01e;
  --head:"Chakra Petch", sans-serif;
  --body:"Inter", sans-serif;
}
*{box-sizing:border-box;margin:0;padding:0}
html,body{width:1200px;height:5096px;overflow:hidden}
body{background:var(--bg);color:var(--text);font-family:var(--body);position:relative}
.abs{position:absolute}
.photo{position:absolute;display:block}
.eyebrow{font-family:var(--body);font-size:11px;letter-spacing:3px;font-weight:600;text-transform:uppercase;color:var(--text)}
.eyebrow::before{content:"";display:block;width:34px;height:2px;background:var(--accent);margin-bottom:6px}
.eyebrow.center::before{margin:0 auto 6px}
.title{font-family:var(--head);font-weight:600;text-transform:uppercase;font-size:38px;line-height:1.12;letter-spacing:1px}
.para{font-size:13px;line-height:1.6;color:var(--muted)}
.btn-outline{display:inline-flex;align-items:center;gap:8px;border:1px solid #fff;border-radius:22px;padding:0 22px;height:40px;font-size:11px;font-weight:700;letter-spacing:1px;color:#fff;text-transform:uppercase}
.btn-outline svg{width:14px;height:14px}

/* top bar + nav */
.topbar{position:absolute;left:0;top:0;width:1200px;height:42px;border-bottom:1px solid rgba(255,255,255,.12);z-index:3}
.topbar .social{position:absolute;left:84px;top:15px;display:flex;gap:14px}
.topbar .social span{width:11px;height:11px;border-radius:50%;background:#fff;display:block}
.topbar .contact{position:absolute;right:96px;top:13px;display:flex;gap:26px;font-size:11px;color:#ddd}
.topbar .contact span{display:flex;align-items:center;gap:6px}
.nav{position:absolute;left:0;top:42px;width:1200px;height:70px;z-index:3}
.brand{display:flex;align-items:center;gap:8px;font-family:var(--body);font-weight:700;font-size:13px;letter-spacing:.5px;text-transform:uppercase;color:#fff;white-space:nowrap}
.brand i{width:11px;height:11px;background:#fff;display:block}
.nav .brand{position:absolute;left:120px;top:27px}
.nav ul{position:absolute;left:312px;top:28px;display:flex;gap:28px;list-style:none;font-size:13px;font-weight:500}
.nav ul li:first-child{border-bottom:2px solid var(--accent);padding-bottom:4px}
.nav .btn-appoint{position:absolute;left:965px;top:16px;height:38px;padding:0 20px;border:1px solid #fff;border-radius:20px;font-size:11px;font-weight:700;letter-spacing:.5px;display:flex;align-items:center}

/* hero */
.hero{position:absolute;left:0;top:0;width:1200px;height:730px;overflow:hidden}
.hero .photo{left:0;top:0;width:1200px;height:730px;background:radial-gradient(ellipse at 62% 45%,#3c3d40 0%,#222326 35%,#0c0c0d 75%),#111}
.hero .shade{position:absolute;left:0;top:0;width:1200px;height:730px;background:linear-gradient(90deg,rgba(0,0,0,.55) 0%,rgba(0,0,0,.05) 55%,rgba(0,0,0,.45) 100%),linear-gradient(180deg,rgba(0,0,0,.6) 0%,rgba(0,0,0,0) 22%,rgba(0,0,0,0) 70%,rgba(21,21,21,1) 100%)}
.hero .kicker{position:absolute;left:186px;top:508px;font-size:13px;letter-spacing:5px;font-weight:600}
.hero h1{position:absolute;left:186px;top:530px;font-family:var(--head);font-weight:700;font-size:46px;letter-spacing:1px;text-transform:uppercase}
.hero .lead{position:absolute;left:872px;top:480px;width:250px;font-size:13px;line-height:1.55;color:#ddd}
.hero .slide-index{position:absolute;left:1096px;top:272px;font-size:12px;font-weight:600}
.hero .slide-index::after{content:"";display:block;width:2px;height:44px;background:#fff;margin:8px 0 0 6px}

/* about */
.about .img-a{left:85px;top:765px;width:240px;height:320px;background:linear-gradient(160deg,#d8d6d2 0%,#8c8a86 45%,#2d2c2b 100%)}
.about .img-b{left:345px;top:830px;width:120px;height:172px;background:linear-gradient(150deg,#2a2a2a 0%,#9c1c22 55%,#3b0c0e 100%)}
.about .eyebrow{left:630px;top:792px}
.about .title{left:630px;top:822px;width:460px}
.about .para{left:630px;top:924px;width:460px}
.about .btn-outline{position:absolute;left:617px;top:1078px}

/* services */
.services .eyebrow{left:85px;top:1248px}
.services .title{left:85px;top:1280px;width:760px}
.svc{position:absolute;top:1410px;width:323px;height:375px;overflow:hidden}
.svc .fill{position:absolute;inset:0}
.svc .fade{position:absolute;inset:0;background:linear-gradient(180deg,rgba(0,0,0,0) 55%,rgba(0,0,0,.85) 100%)}
.svc h3{position:absolute;left:14px;bottom:44px;font-size:14px;font-weight:700;text-transform:uppercase;border-bottom:2px solid var(--accent);padding-bottom:3px}
.svc p{position:absolute;left:14px;bottom:12px;width:170px;font-size:10px;line-height:1.45;color:#ccc}
.svc .more{position:absolute;right:14px;bottom:18px;display:flex;align-items:center;gap:5px;font-size:10px;font-weight:700}

/* gallery */
.gallery{position:absolute;left:0;top:1845px;width:1200px;height:735px;background:var(--bg-band)}
.gallery .eyebrow{position:absolute;left:0;top:62px;width:1200px;text-align:center}
.gallery .title{position:absolute;left:0;top:96px;width:1200px;text-align:center}
.gallery .photo{box-shadow:0 10px 30px rgba(0,0,0,.6)}
.gallery .arrows{position:absolute;left:556px;top:606px;display:flex;gap:12px}
.gallery .arrows span{width:38px;height:38px;border:1px solid #fff;border-radius:50%;display:flex;align-items:center;justify-content:center}

/* lounge */
.lounge .eyebrow{left:85px;top:2660px}
.lounge .title{left:85px;top:2696px}
.lounge .para{left:615px;top:2654px;width:500px}
.lounge .btn-outline{position:absolute;left:615px;top:2748px}
.lcard{position:absolute;top:2830px;width:323px;height:325px;overflow:hidden}
.lcard .fill{position:absolute;inset:0}
.lcard .fade{position:absolute;inset:0;background:linear-gradient(180deg,rgba(0,0,0,0) 55%,rgba(0,0,0,.85) 100%)}
.lcard h3{position:absolute;left:14px;bottom:42px;font-size:14px;font-weight:700;text-transform:uppercase;border-bottom:2px solid var(--accent);padding-bottom:3px}
.lcard p{position:absolute;left:14px;bottom:10px;width:280px;font-size:10px;line-height:1.45;color:#ccc}

/* testimonials */
.reviews .eyebrow{left:85px;top:3252px}
.reviews .title{left:85px;top:3284px}
.rating{position:absolute;left:85px;top:3334px;display:flex;align-items:center;gap:8px;font-size:11px;color:#ddd}
.rating b{font-size:18px;font-weight:700;color:#fff}
.stars{color:var(--star);letter-spacing:2px;font-size:13px}
.review{position:absolute;top:3382px;width:245px;height:358px;background:var(--card);padding:22px 20px}
.review .top{display:flex;justify-content:space-between;align-items:center}
.review .badge{width:16px;height:16px;border-radius:50%;background:#dcdcdc}
.review .body{margin-top:22px;font-size:11px;line-height:1.6;color:#cfcfcf}
.review .who{position:absolute;left:20px;bottom:42px;font-size:13px;font-weight:600;border-top:1px solid var(--line);width:205px;padding-top:26px}
.review .role{position:absolute;left:20px;bottom:24px;font-size:10px;color:var(--muted)}

/* contact */
.contact-sec{position:absolute;left:0;top:3915px;width:1200px;height:565px;overflow:hidden}
.contact-sec .bg{left:0;top:0;width:1200px;height:565px;background:radial-gradient(ellipse at 50% 30%,#3a3a3c 0%,#1d1d1f 55%,#0e0e0f 100%)}
.contact-sec .map{left:155px;top:135px;width:495px;height:360px;background:linear-gradient(135deg,#e9ece9 0%,#d6e2d6 50%,#cfd8e3 100%)}
.form{position:absolute;left:672px;top:110px;width:360px;height:410px;background:rgba(20,20,20,.85);padding:26px 18px}
.form .title{font-size:36px;margin-top:8px}
.field{height:36px;border-bottom:1px solid #5a5a5a;font-size:11px;color:#bbb;display:flex;align-items:center;justify-content:space-between;padding:0 2px}
.form .fields{margin-top:14px}
.form .message{height:58px;align-items:flex-start;padding-top:10px}
.form .submit{margin-top:20px;height:38px;border-radius:20px;background:#fff;color:#111;display:flex;align-items:center;justify-content:center;gap:8px;font-size:11px;font-weight:700}

/* footer */
.footer{position:absolute;left:0;top:4480px;width:1200px;height:616px;background:var(--bg-deep)}
.footer .strap{position:absolute;left:85px;top:38px;font-family:var(--head);font-weight:600;font-size:36px;text-transform:uppercase;letter-spacing:1px}
.footer .totop{position:absolute;left:1028px;top:50px;display:flex;align-items:center;gap:6px;font-size:11px;font-weight:700}
.footer .rule{position:absolute;left:85px;top:100px;width:1030px;height:1px;background:var(--line)}
.footer .brand{position:absolute;left:130px;top:206px;font-size:17px}
.footer .brand i{width:13px;height:13px}
.footer .divider{position:absolute;left:410px;top:130px;width:1px;height:370px;background:var(--line)}
.fcol{position:absolute;top:170px;font-size:12px;color:#ccc;line-height:1.7}
.fcol h4{font-size:14px;font-weight:700;color:#fff;text-transform:uppercase;margin-bottom:10px}
.fcol .row{display:flex;gap:8px;align-items:flex-start;margin-bottom:4px}
.fcol ul{list-style:none}
.fcol .social{display:flex;gap:16px;margin-top:6px}
.fcol .social span{width:12px;height:12px;border-radius:50%;background:#fff;display:block}
.footer .bottom{position:absolute;left:0;top:560px;width:1200px;height:56px;border-top:1px solid var(--line);font-size:10px;color:#999;display:flex;align-items:center;justify-content:space-between;padding:0 85px}
</style>
</head>
<body>

<!-- HERO -->
<section class="hero">
  <div class="photo" role="img" aria-label="Dark black luxury SUV parked inside the detailing studio under hexagonal ceiling lights"></div>
  <div class="shade"></div>
  <div class="kicker">PREMIUM AUTOMOTIVE</div>
  <h1>Detailing Studio</h1>
  <p class="lead">Morbi enim quam, aliquet ut eleifend pretium, scelerisque at nibh. Etiam facilisis cursus pellentesque. Donec fermentum ligula nulla, in egestas dolor fermentum.</p>
  <div class="slide-index">01</div>
</section>

<header class="topbar">
  <div class="social"><span></span><span></span><span></span></div>
  <div class="contact">
    <span><svg width="11" height="11" viewBox="0 0 24 24" fill="#fff"><path d="M6.6 10.8a15.5 15.5 0 0 0 6.6 6.6l2.2-2.2c.3-.3.7-.4 1-.2 1.1.4 2.3.6 3.6.6.6 0 1 .4 1 1V20c0 .6-.4 1-1 1A17 17 0 0 1 3 4c0-.6.4-1 1-1h3.5c.6 0 1 .4 1 1 0 1.3.2 2.5.6 3.6.1.3 0 .7-.2 1z"/></svg>Call Us : 1800 555 014</span>
    <span><svg width="12" height="10" viewBox="0 0 24 20" fill="none" stroke="#fff" stroke-width="2"><rect x="1" y="1" width="22" height="18" rx="2"/><path d="M1 3l11 8 11-8"/></svg>Message us : support@velourdetailing.com</span>
  </div>
</header>

<nav class="nav">
  <div class="brand"><i></i>Velour Detailing</div>
  <ul>
    <li>Home</li><li>About</li><li>Services</li><li>Gallery</li><li>Client Lounge</li><li>Testimonials</li><li>Contact Us</li>
  </ul>
  <div class="btn-appoint">MAKE APPOINTMENT</div>
</nav>

<!-- ABOUT -->
<section class="about">
  <div class="photo img-a" role="img" aria-label="Detailer in a work apron polishing a car inside the studio"></div>
  <div class="photo img-b" role="img" aria-label="Close view of a red car headlight after polishing"></div>
  <div class="abs eyebrow">About Us</div>
  <h2 class="abs title">Restoring Lasting<br>Shine, Inside and Out</h2>
  <p class="abs para">Cras fermentum lectus nec elit tincidunt semper. Mauris at diam at tellus mattis rhoncus vitae eu mi. Etiam rhoncus ut vitae semper facilisis. Aenean eu posuere lorem. Vivamus aliquam tellus velit. Donec ornare, tortor eu pulvinar, lorem sed suscipit ex, a euismod lacus lectus ut quam.</p>
  <div class="btn-outline"><svg viewBox="0 0 24 24" fill="none" stroke="#fff" stroke-width="2"><path d="M6 3h12l3 6-9 12L3 9z"/><path d="M3 9h18"/></svg>Read More</div>
</section>

<!-- SERVICES -->
<section class="services">
  <div class="abs eyebrow">Services</div>
  <h2 class="abs title">Velour Detailing Services That<br>Go Beyond Expectations</h2>

  <article class="svc" style="left:85px">
    <div class="fill" role="img" aria-label="Detailer machine-polishing the bonnet of a blue car" style="background:linear-gradient(160deg,#8a8f96 0%,#3d4a66 45%,#142040 100%)"></div>
    <div class="fade"></div>
    <h3>Detailing</h3>
    <p>Vivamus aliquam tellus velit. Donec ornare, tortor eu pulvinar.</p>
    <div class="more"><svg width="11" height="11" viewBox="0 0 24 24" fill="none" stroke="#fff" stroke-width="2"><path d="M6 3h12l3 6-9 12L3 9z"/></svg>READ MORE</div>
  </article>
  <article class="svc" style="left:440px">
    <div class="fill" role="img" aria-label="Gloved hand applying ceramic coating to a red car" style="background:linear-gradient(150deg,#6b6b6b 0%,#8e1a1f 50%,#2a0a0b 100%)"></div>
    <div class="fade"></div>
    <h3>Ceramic Coating</h3>
    <p>Vivamus aliquam tellus velit. Donec ornare, tortor eu.</p>
    <div class="more"><svg width="11" height="11" viewBox="0 0 24 24" fill="none" stroke="#fff" stroke-width="2"><path d="M6 3h12l3 6-9 12L3 9z"/></svg>READ MORE</div>
  </article>
  <article class="svc" style="left:792px">
    <div class="fill" role="img" aria-label="Technician cleaning a car interior beside colour swatches" style="background:linear-gradient(160deg,#b9b4ad 0%,#5a5652 45%,#1c1c1c 100%)"></div>
    <div class="fade"></div>
    <h3>Interior</h3>
    <p>Vivamus aliquam tellus velit. Donec ornare, tortor eu.</p>
    <div class="more"><svg width="11" height="11" viewBox="0 0 24 24" fill="none" stroke="#fff" stroke-width="2"><path d="M6 3h12l3 6-9 12L3 9z"/></svg>READ MORE</div>
  </article>
</section>

<!-- GALLERY -->
<section class="gallery">
  <div class="eyebrow center">Gallery</div>
  <h2 class="title">View Our Work</h2>
  <div class="photo" role="img" aria-label="Car detail work photo" style="left:112px;top:210px;width:140px;height:240px;background:linear-gradient(160deg,#7e7e7e,#2a2a2a)"></div>
  <div class="photo" role="img" aria-label="Detailer working on a car door" style="left:245px;top:190px;width:185px;height:290px;background:linear-gradient(160deg,#9a9a9a,#333)"></div>
  <div class="photo" role="img" aria-label="Yellow polishing pad on a car panel" style="left:764px;top:190px;width:190px;height:290px;background:linear-gradient(160deg,#8fa3b8,#2a3440)"></div>
  <div class="photo" role="img" aria-label="Car wheel and bodywork after cleaning" style="left:945px;top:210px;width:140px;height:240px;background:linear-gradient(160deg,#7c7c7c,#252525)"></div>
  <div class="photo" role="img" aria-label="Detailer polishing a car with a yellow rotary polisher" style="left:440px;top:175px;width:322px;height:400px;background:linear-gradient(160deg,#a8a8a8 0%,#5b5b5b 40%,#c9a527 62%,#2a2a2a 100%)"></div>
  <div class="arrows">
    <span><svg width="12" height="12" viewBox="0 0 24 24" fill="none" stroke="#fff" stroke-width="2"><path d="M20 12H4M10 6l-6 6 6 6"/></svg></span>
    <span><svg width="12" height="12" viewBox="0 0 24 24" fill="none" stroke="#fff" stroke-width="2"><path d="M4 12h16M14 6l6 6-6 6"/></svg></span>
  </div>
</section>

<!-- CLIENT LOUNGE -->
<section class="lounge">
  <div class="abs eyebrow">Lounge Area</div>
  <h2 class="abs title">Client Lounge Area</h2>
  <p class="abs para">Vivamus facilisis vel iaculis ante. Etiam faucibus finibus interdum. Etiam ex tortor, aliquam et suscipit in, vulputate id justo. Phasellus a quam at erat pulvinar finibus ac non elit.</p>
  <div class="btn-outline"><svg viewBox="0 0 24 24" fill="none" stroke="#fff" stroke-width="2"><path d="M6 3h12l3 6-9 12L3 9z"/><path d="M3 9h18"/></svg>Read More</div>

  <article class="lcard" style="left:85px">
    <div class="fill" role="img" aria-label="Guest relaxing on a blue lounge sofa" style="background:linear-gradient(160deg,#d9dde2 0%,#8495ab 50%,#2b3240 100%)"></div>
    <div class="fade"></div>
    <h3>Comfort Zone</h3>
    <p>Vivamus aliquam tellus velit. Donec ornare, tortor eu pulvinar.</p>
  </article>
  <article class="lcard" style="left:440px">
    <div class="fill" role="img" aria-label="Two guests enjoying coffee in the studio cafe area" style="background:linear-gradient(160deg,#e7e2da 0%,#a98f74 50%,#3a2d22 100%)"></div>
    <div class="fade"></div>
    <h3>Coffee Area</h3>
    <p>Vivamus aliquam tellus velit. Donec ornare, tortor eu pulvinar.</p>
  </article>
  <article class="lcard" style="left:792px">
    <div class="fill" role="img" aria-label="Guest waiting in a bright seating area with a phone" style="background:linear-gradient(160deg,#eeeeea 0%,#a9a8a2 50%,#35342f 100%)"></div>
    <div class="fade"></div>
    <h3>Waiting Space</h3>
    <p>Vivamus aliquam tellus velit. Donec ornare, tortor eu pulvinar.</p>
  </article>
</section>

<!-- TESTIMONIALS -->
<section class="reviews">
  <div class="abs eyebrow">Testimonials</div>
  <h2 class="abs title">Our Trusted Reviews</h2>
  <div class="rating"><b>Trusted</b><span class="stars">★★★★★</span><span>4.9 rating of 20,000</span></div>

  <article class="review" style="left:85px">
    <div class="top"><span class="stars">★★★★★</span><span class="badge"></span></div>
    <p class="body">Donec non ante at enim faucibus eleifend laoreet non dui. Phasellus at diam neque. Praesent sed elit felis. Nullam ullamcorper erat, in mattis ex vehicula ac. Sed ex urna, fermentum vitae sagittis ac, molestie quis sem. Sed in lobortis ipsum. Curabitur et mauris dapibus.</p>
    <div class="who">Elias Marrow</div>
    <div class="role">Customer</div>
  </article>
  <article class="review" style="left:347px">
    <div class="top"><span class="stars">★★★★★</span><span class="badge"></span></div>
    <p class="body">Donec non ante at enim faucibus eleifend laoreet non dui. Phasellus at diam neque. Praesent sed elit felis. Nullam ullamcorper erat, in mattis ex vehicula ac. Sed ex urna, fermentum vitae sagittis ac, molestie quis sem. Sed in lobortis ipsum. Curabitur et mauris dapibus.</p>
    <div class="who">Elias Marrow</div>
    <div class="role">Customer</div>
  </article>
  <article class="review" style="left:608px">
    <div class="top"><span class="stars">★★★★★</span><span class="badge"></span></div>
    <p class="body">Donec non ante at enim faucibus eleifend laoreet non dui. Phasellus at diam neque. Praesent sed elit felis. Nullam ullamcorper erat, in mattis ex vehicula ac. Sed ex urna, fermentum vitae sagittis ac, molestie quis sem. Sed in lobortis ipsum. Curabitur et mauris dapibus.</p>
    <div class="who">Elias Marrow</div>
    <div class="role">Customer</div>
  </article>
  <article class="review" style="left:870px">
    <div class="top"><span class="stars">★★★★★</span><span class="badge"></span></div>
    <p class="body">Donec non ante at enim faucibus eleifend laoreet non dui. Phasellus at diam neque. Praesent sed elit felis. Nullam ullamcorper erat, in mattis ex vehicula ac. Sed ex urna, fermentum vitae sagittis ac, molestie quis sem. Sed in lobortis ipsum. Curabitur et mauris dapibus.</p>
    <div class="who">Elias Marrow</div>
    <div class="role">Customer</div>
  </article>
</section>

<!-- CONTACT -->
<section class="contact-sec">
  <div class="photo bg" role="img" aria-label="Dim studio interior with hexagonal ceiling lights"></div>
  <div class="photo map" role="img" aria-label="Street map showing the studio location"></div>
  <div class="form">
    <div class="eyebrow">Contact Us</div>
    <h2 class="title">Get In Touch</h2>
    <div class="fields">
      <div class="field">Name</div>
      <div class="field">Email</div>
      <div class="field">Phone</div>
      <div class="field">Select Subject <svg width="10" height="10" viewBox="0 0 24 24" fill="none" stroke="#bbb" stroke-width="2"><path d="M6 9l6 6 6-6"/></svg></div>
      <div class="field message">Message</div>
    </div>
    <div class="submit"><svg width="12" height="12" viewBox="0 0 24 24" fill="none" stroke="#111" stroke-width="2"><path d="M6 3h12l3 6-9 12L3 9z"/></svg>SUBMIT</div>
  </div>
</section>

<!-- FOOTER -->
<footer class="footer">
  <div class="strap">Premium Automotive Detailing Studio</div>
  <div class="totop">GO TO TOP <svg width="10" height="10" viewBox="0 0 24 24" fill="none" stroke="#fff" stroke-width="2"><path d="M12 20V4M6 10l6-6 6 6"/></svg></div>
  <div class="rule"></div>
  <div class="brand"><i></i>Velour Detailing</div>
  <div class="divider"></div>

  <div class="fcol" style="left:445px">
    <h4>Address</h4>
    <div class="row"><svg width="11" height="14" viewBox="0 0 24 30" fill="#fff"><path d="M12 0a10 10 0 0 0-10 10c0 8 10 20 10 20s10-12 10-20A10 10 0 0 0 12 0zm0 14a4 4 0 1 1 0-8 4 4 0 0 1 0 8z"/></svg><span>48 Harbor Row Suite 210<br>Larkmoor</span></div>
    <h4 style="margin-top:18px">Contact Info</h4>
    <div class="row"><svg width="11" height="11" viewBox="0 0 24 24" fill="#fff"><path d="M6.6 10.8a15.5 15.5 0 0 0 6.6 6.6l2.2-2.2c.3-.3.7-.4 1-.2 1.1.4 2.3.6 3.6.6.6 0 1 .4 1 1V20c0 .6-.4 1-1 1A17 17 0 0 1 3 4c0-.6.4-1 1-1h3.5c.6 0 1 .4 1 1 0 1.3.2 2.5.6 3.6.1.3 0 .7-.2 1z"/></svg><span>1800 555 014</span></div>
    <div class="row"><svg width="12" height="10" viewBox="0 0 24 20" fill="none" stroke="#fff" stroke-width="2"><rect x="1" y="1" width="22" height="18" rx="2"/><path d="M1 3l11 8 11-8"/></svg><span>support@velourdetailing.com</span></div>
  </div>

  <div class="fcol" style="left:775px">
    <h4>Quick Links</h4>
    <ul><li>Home</li><li>About</li><li>Services</li><li>Gallery</li><li>Client Lounge</li><li>Testimonials</li><li>Contact Us</li></ul>
  </div>

  <div class="fcol" style="left:1000px">
    <h4>Follow Us</h4>
    <div class="social"><span></span><span></span><span></span></div>
  </div>

  <div class="bottom"><span>© 2025 VELOUR DETAILING · ALL RIGHTS RESERVED</span><span>Updated July 2025</span></div>
</footer>

</body>
</html>
```